Book Title: The Weaver's Lantern. Author Name: Maribel Trowcastle

We are needing a cover, spine and back cover design for a poetry book that we are publishing called The Weaver's Lantern. We are looking for an elegant, and simplistic design with a very natural, dynamic and powerful impact.

Design Idea #1 - Shiva Conch Shell with a pink or black background. See Paul Renwick Image attached for design inspiration. Simple and dynamic .
Title and Author name created in same style as the attached Paul Renwick's Harbors and Lanterns image.

Design Idea #2 - Image of cauldron on (see cauldrons attached for ideas) black background.
See Paul Renwick Image attached for design inspiration. Simple and dynamic Title and Author name created in same style as the attached Paul Renwick's Harbors and Lanterns image

Design Idea #3 - Image of Tree of Life (see attached images for idea of what we are looking for) Would like to see on plain white, green, black and green background.

Target Market(s)

Spiritual Women, healers, visionaries,Goddess'

Requirements
Must have
• Please see project descriptions for specific design concepts we are looking for. Please include the authors name: Maribel Trowcastle on front, spine and back cover of the book

```html
<!DOCTYPE html>
<html lang="en">
<head>
<meta charset="utf-8">
<title>The Weaver's Lantern — Cover</title>
<link rel="stylesheet" href="https://fonts.googleapis.com/css2?family=EB+Garamond:wght@500&display=swap">
<style>
  :root {
    --backdrop: #bd8c63;
    --cover-black: #17181b;
    --cover-black-deep: #0f1014;
    --gold: #c3976b;
    --emblem-gold: #a8805a;
    --emblem-gold-light: #b98f66;
  }
  html, body {
    margin: 0;
    padding: 0;
    width: 1200px;
    height: 1200px;
    overflow: hidden;
    background: var(--backdrop);
  }
  .canvas {
    position: relative;
    width: 1200px;
    height: 1200px;
  }
  .book-cover {
    position: absolute;
    left: 237px;
    top: 50px;
    width: 726px;
    height: 1100px;
    background: linear-gradient(160deg, var(--cover-black) 0%, var(--cover-black-deep) 100%);
    font-family: "EB Garamond", Georgia, serif;
    font-weight: 500;
    color: var(--gold);
    text-align: center;
  }
  .hinge {
    position: absolute;
    left: 0;
    top: 0;
    width: 50px;
    height: 100%;
    background: linear-gradient(90deg, rgba(255,255,255,0.02), rgba(0,0,0,0.15));
    border-right: 1px solid rgba(0,0,0,0.25);
  }
  .title {
    position: absolute;
    left: 0;
    right: 0;
    top: 71px;
    margin: 0;
    font-size: 50px;
    font-weight: 500;
    line-height: 72px;
    letter-spacing: 0.42em;
    text-transform: uppercase;
    padding-left: 0.42em;
  }
  .title span { display: block; }
  .emblem {
    position: absolute;
    left: 50%;
    top: 473px;
    width: 196px;
    height: 196px;
    margin-left: -98px;
  }
  .author {
    position: absolute;
    left: 0;
    right: 0;
    top: 888px;
    margin: 0;
    font-size: 56px;
    line-height: 72px;
    letter-spacing: 0.32em;
    padding-left: 0.32em;
  }
  .author span { display: block; }
</style>
</head>
<body>
  <div class="canvas">
    <div class="book-cover">
      <div class="hinge"></div>
      <h1 class="title">
        <span>The</span>
        <span>Weaver's</span>
        <span>Lantern</span>
      </h1>
      <svg class="emblem" viewBox="0 0 196 196" role="img" aria-label="Gold line illustration of a tree of life with a leafy round crown and spreading roots, set in a circle">
        <defs>
          <linearGradient id="emblemFill" x1="0" y1="0" x2="0" y2="1">
            <stop offset="0%" stop-color="#b98f66"/>
            <stop offset="100%" stop-color="#a8805a"/>
          </linearGradient>
        </defs>
        <circle cx="98" cy="98" r="97" fill="url(#emblemFill)"/>
      </svg>
      <p class="author">
        <span>Maribel</span>
        <span>Trowcastle</span>
      </p>
    </div>
  </div>
</body>
</html>
```